Laser Tattoo Removal Business Cards

We are looking for a professional business card design for a laser tattoo removal business. Ideally looking for a black business card design. The name of the business is Brightline Tattoo Removal. We place our cards at local tattoo shops so we ideally are looking for something trendy/edgy to draw both male and female clientele in.

Target Market(s)

Male/Female ages 18-60

Contact Information for Business Card

black background ideally.. hoping to stay within greys, whites and black

Font styles to use
Serif
Sans Serif

Colors
121212
a9a9a9
5c5c5c
f5f5f5
ffffff
7f7f7f
606060
848484
9d9d9d

Requirements
Must have
• Employee Info:
• Melissa Thornbury
• Chief Executive Offer
• m: 919.537.2846
• w: 919.362.4178
• f: 919.685.3907
• mthornbury@brightlinetattooremoval.example
• Address:
• 4615 Oakmere Pkwy, Suite 210
• Raleigh, NC 27654
• Website:
• www.brightlinetattooremoval.example
Nice to have
• Myabe business name on back or logo on back and employee info on the front

```html
<!DOCTYPE html>
<html lang="en">
<head>
<meta charset="utf-8">
<title>Brightline Tattoo Removal – Business Cards</title>
<link rel="stylesheet" href="https://fonts.googleapis.com/css2?family=Lato:wght@400;700&display=swap">
<style>
  :root {
    --backdrop: #2a2624;
    --card: #121212;
    --white: #ffffff;
    --offwhite: #f5f5f5;
    --light-grey: #a9a9a9;
    --mid-grey: #848484;
    --rule: #5c5c5c;
  }
  * { margin: 0; padding: 0; box-sizing: border-box; }
  html, body {
    width: 1200px;
    height: 844px;
    overflow: hidden;
    background: var(--backdrop);
    font-family: "Lato", Arial, sans-serif;
  }
  .canvas {
    position: relative;
    width: 1200px;
    height: 844px;
  }
  .card {
    position: absolute;
    top: 272px;
    width: 520px;
    height: 300px;
    background: var(--card);
    color: var(--offwhite);
  }
  .card--front { left: 50px; }
  .card--back { left: 630px; }

  .wordmark {
    text-align: center;
    color: var(--white);
    font-weight: 400;
    text-transform: uppercase;
    line-height: 1;
  }
  .wordmark__name {
    display: block;
    font-size: 34px;
    letter-spacing: 3px;
  }
  .wordmark__tagline {
    display: block;
    margin-top: 10px;
    font-size: 13px;
    letter-spacing: 3px;
  }

  /* front */
  .card--front .wordmark {
    position: absolute;
    top: 34px;
    right: 34px;
    width: 240px;
  }
  .card--front .wordmark__name { font-size: 30px; }
  .card--front .wordmark__tagline { font-size: 11px; }
  .rule {
    position: absolute;
    left: 34px;
    right: 34px;
    height: 1px;
    background: var(--rule);
  }
  .rule--top { top: 112px; }
  .rule--bottom { top: 252px; }
  .person {
    position: absolute;
    left: 34px;
    top: 128px;
  }
  .person__name {
    font-size: 17px;
    font-weight: 700;
    letter-spacing: 0.5px;
    color: var(--light-grey);
    text-transform: uppercase;
  }
  .person__title {
    font-size: 13px;
    color: var(--mid-grey);
    margin-top: 2px;
  }
  .contact {
    position: absolute;
    left: 34px;
    top: 186px;
    font-size: 13px;
    line-height: 1.55;
    color: var(--light-grey);
    list-style: none;
  }
  .contact b { color: var(--offwhite); font-weight: 700; }
  .contact .sep { color: var(--rule); margin: 0 6px; }
  .address {
    position: absolute;
    left: 34px;
    top: 266px;
    font-size: 13px;
    color: var(--light-grey);
  }

  /* back */
  .card--back .wordmark {
    position: absolute;
    top: 92px;
    left: 0;
    right: 0;
  }
  .website {
    position: absolute;
    top: 196px;
    left: 0;
    right: 0;
    text-align: center;
    font-size: 13px;
    color: var(--offwhite);
  }
</style>
</head>
<body>
<main class="canvas">
  <section class="card card--front" aria-label="Card front">
    <div class="wordmark">
      <span class="wordmark__name">Brightline</span>
      <span class="wordmark__tagline">Tattoo Removal</span>
    </div>
    <div class="rule rule--top"></div>
    <div class="person">
      <p class="person__name">Melissa Thornbury</p>
      <p class="person__title">Chief Executive Officer</p>
    </div>
    <ul class="contact">
      <li><b>M:</b> 919.537.2846<span class="sep">|</span><b>W:</b> 919.362.4178<span class="sep">|</span><b>F:</b> 919.685.3907</li>
      <li><b>E:</b> mthornbury@brightlinetattooremoval.example</li>
    </ul>
    <div class="rule rule--bottom"></div>
    <p class="address">4615 Oakmere Pkwy, Suite 210 Raleigh, NC 27654</p>
  </section>

  <section class="card card--back" aria-label="Card back">
    <div class="wordmark">
      <span class="wordmark__name">Brightline</span>
      <span class="wordmark__tagline">Tattoo Removal</span>
    </div>
    <p class="website">www.brightlinetattooremoval.example</p>
  </section>
</main>
</body>
</html>
```